We need a complete design for our construction company KELTO CONSTRUCTION based in Auckland New Zealand, we need a logo, website, business card, vehicle design etc..
We are a mid to high-end construction company who work mostly on residential projects and some commercial.

What we want to see in the design;
Professional,
Architectural,
Simple,
Alternative,

We want the design to communicate professionalism, high quality wormanship and and quality service.

Target Market(s)

People looking for a quality building/ construction company

Industry/Entity Type

Construction Company

Contact Information for Business Card

KELTO CONSTRUCTION.co.nz
Lino Verasek
lino@keltoconstruction.example.nz
021 5807 462

Logo Text

KELTO CONSTRUCTION

Number of Pages Required

5+ page

Font styles to use
Sans Serif

Colors

Designer to choose colors to be used in the design.

Requirements
Must have
• Must appear high end, professional, quality, be simple, easy to use, give security to potential clients
Nice to have
• high-quality photos of our recent projects
• about us page
• blog page
• contact us page
• high quality content
Should not have
• should not be hard to use and have too much going on.

```html
<!DOCTYPE html>
<html lang="en">
<head>
<meta charset="utf-8">
<title>Kelto Construction</title>
<link href="https://fonts.googleapis.com/css2?family=Montserrat:wght@400;600;700;800&family=Open+Sans:wght@400;600&display=swap" rel="stylesheet">
<style>
:root{
  --blue:#1b8fe2;
  --blue-dark:#1477c4;
  --ink:#2b2b2b;
  --text:#555;
  --light:#ececee;
  --rule:#dcdcdc;
  --white:#fff;
}
*{box-sizing:border-box;margin:0;padding:0}
html,body{width:1200px;height:3364px;overflow:hidden;background:var(--white)}
body{position:relative;font-family:'Open Sans',sans-serif;color:var(--text)}
.section{position:absolute;left:0;width:1200px}
h2,h3,h4,.nav,.btn,.brand{font-family:'Montserrat',sans-serif}
.btn{display:inline-block;background:var(--blue);color:var(--white);font-weight:700;text-transform:uppercase;letter-spacing:.5px}

/* hero */
.hero{top:0;height:635px}
.hero-photo{position:absolute;inset:0;background:
  linear-gradient(180deg,rgba(0,0,0,.35) 0%,rgba(0,0,0,.05) 18%,rgba(0,0,0,0) 60%),
  linear-gradient(180deg,#6f8a5a 0%,#4f6b3e 22%,#7a4a36 40%,#8b5a43 62%,#3f5a2a 80%,#6fa03e 100%)}
.brand{position:absolute;left:130px;top:14px;color:var(--white);font-size:29px;font-weight:400}
.brand b{font-weight:800}
.nav{position:absolute;right:146px;top:22px;display:flex;gap:8px;align-items:center}
.nav a{color:var(--white);font-size:11px;font-weight:700;text-decoration:none;padding:6px 10px;text-transform:uppercase}
.nav a.active{background:var(--blue)}
.nav .search{width:24px;height:24px;border:2px solid var(--white);border-radius:50%;display:flex;align-items:center;justify-content:center;margin-left:6px}
.hero h1{position:absolute;top:242px;left:0;width:1200px;text-align:center;font-family:'Montserrat',sans-serif;color:var(--white);font-size:27px;font-weight:800;line-height:36px;text-transform:uppercase}
.hero .btn{position:absolute;left:517px;top:333px;width:148px;height:38px;line-height:38px;text-align:center;font-size:15px;border:2px solid rgba(255,255,255,.8)}
.dots{position:absolute;top:560px;left:553px;display:flex;gap:9px}
.dots span{width:10px;height:10px;border-radius:50%;background:var(--white)}
.dots span.on{background:var(--blue);box-shadow:0 0 0 2px var(--white)}

/* titles */
.title{position:absolute;left:0;width:1200px;text-align:center;font-size:20px;font-weight:800;color:var(--ink);text-transform:uppercase}
.title::after{content:"";display:block;width:48px;height:2px;background:#999;margin:20px auto 0}
.title.light{color:var(--white)}
.title.light::after{background:var(--white)}

/* services */
.services{top:635px;height:632px}
.svc-grid{position:absolute;left:128px;top:139px;width:937px;display:grid;grid-template-columns:316px 321px 300px;grid-template-rows:213px 224px}
.svc{text-align:center;padding-top:18px;border-color:var(--rule);border-style:solid;border-width:0}
.svc:nth-child(-n+3){border-bottom-width:1px}
.svc:nth-child(3n+1),.svc:nth-child(3n+2){border-right-width:1px}
.svc svg{width:80px;height:72px}
.svc h4{font-size:13px;font-weight:700;color:var(--ink);margin:22px 0 10px;text-transform:uppercase}
.svc p{font-size:11px;line-height:16px;width:212px;margin:0 auto}

/* welcome */
.welcome{top:1267px;height:550px;color:var(--white)}
.welcome-photo{position:absolute;inset:0;background:linear-gradient(180deg,#7877d4 0%,#8a84d8 35%,#9b88c6 55%,#5a4f6a 75%,#2d2621 100%)}
.welcome-split{position:absolute;left:621px;top:0;width:2px;height:440px;background:rgba(255,255,255,.5)}
.welcome h3{position:absolute;left:146px;top:60px;font-size:18px;font-weight:800;text-transform:uppercase}
.welcome h3::after{content:"";display:block;width:98px;height:3px;background:var(--white);margin-top:10px}
.welcome .intro{position:absolute;left:150px;top:133px;width:400px;font-size:12px;line-height:18px}
.welcome .btn-outline{position:absolute;left:150px;top:219px;width:113px;height:32px;line-height:32px;text-align:center;background:var(--white);color:var(--ink);font-family:'Montserrat',sans-serif;font-size:13px;font-weight:700}
.feature{position:absolute;left:714px;display:flex;gap:24px;width:330px}
.feature .ico{flex:0 0 70px;height:70px;border-radius:50%;border:3px solid var(--white);display:flex;align-items:center;justify-content:center}
.feature h4{font-size:13px;font-weight:700;margin:5px 0 6px;text-transform:uppercase}
.feature p{font-size:11.5px;line-height:16px;opacity:.9}

/* projects */
.projects{top:1817px;height:680px;background:var(--light)}
.proj-grid{position:absolute;left:179px;top:130px;width:844px;display:grid;grid-template-columns:repeat(3,276px);grid-auto-rows:209px;gap:6px 8px}
.proj{display:block}
.p1{background:linear-gradient(180deg,#8fb0c4,#5f6f6a 55%,#3c5a38)}
.p2{background:linear-gradient(180deg,#9db5c8,#8a6e55 50%,#4f6b3a)}
.p3{background:linear-gradient(180deg,#b0c8dc,#6f7560 50%,#5a7a45)}
.p4{background:linear-gradient(180deg,#6da6d8,#8fb6d6 50%,#7f8d86)}
.p5{background:linear-gradient(180deg,#c6788a,#5b6e9c 45%,#3c4f74)}
.p6{background:linear-gradient(180deg,#5a9be0,#9a4a38 45%,#6f8450)}
.projects .ghost{position:absolute;left:175px;top:568px;font-family:'Montserrat',sans-serif;font-size:60px;font-weight:800;color:#d6d6d8;letter-spacing:1px}
.projects .btn{position:absolute;left:920px;top:578px;width:101px;height:32px;line-height:32px;text-align:center;font-size:13px}

/* blog */
.blog{top:2497px;height:513px}
.blog-photo{position:absolute;inset:0;background:linear-gradient(180deg,#2f7fd0 0%,#5ca2e0 30%,#a9cbe6 55%,#7d9a6a 78%,#5b7f3b 100%)}
.cards{position:absolute;left:135px;top:161px;display:flex;gap:16px}
.card{width:302px;height:265px;background:rgba(255,255,255,.88);padding:32px 0 0 30px;position:relative}
.card .num{position:absolute;left:25px;top:38px;width:20px;height:20px;background:var(--blue);color:var(--white);font-size:10px;text-align:center;line-height:20px}
.card h4{margin-left:35px;width:200px;font-size:13px;font-weight:800;color:var(--ink);line-height:16px;text-transform:uppercase}
.card p{margin:20px 0 0 35px;width:190px;font-size:11.5px;line-height:16px;color:var(--text)}
.card .btn{position:absolute;left:65px;top:216px;width:86px;height:24px;line-height:24px;text-align:center;font-size:11px}

/* footer */
.footer{top:3010px;height:354px;background:var(--blue);color:var(--white)}
.footer .brand{left:130px;top:76px;font-size:29px}
.follow{position:absolute;left:162px;top:151px;display:flex;align-items:center;gap:10px;font-family:'Montserrat',sans-serif;font-size:11px;font-weight:700}
.follow span.dot{width:26px;height:26px;border-radius:50%;background:var(--blue-dark);border:2px solid rgba(255,255,255,.6)}
.follow span.dot.dark{background:#0d2a55}
.fcol{position:absolute;top:52px;font-size:11px;line-height:17px}
.fcol h5{font-family:'Montserrat',sans-serif;font-size:11px;font-weight:700;margin-bottom:14px;text-transform:uppercase}
.contact-col{left:467px;width:160px}
.contact-col .row{display:flex;gap:12px;margin-bottom:10px}
.menu-col{left:642px}
.menu-col a{display:block;color:var(--white);text-decoration:none}
.map{position:absolute;left:749px;top:52px;width:319px;height:172px;background:linear-gradient(135deg,#eeece6,#dfe4df 50%,#e8e4da)}
.rule{position:absolute;left:130px;top:265px;width:940px;height:1px;background:rgba(255,255,255,.35)}
.copy{position:absolute;top:302px;left:0;width:1200px;text-align:center;font-size:11px}
</style>
</head>
<body>

<header class="section hero">
  <div class="hero-photo" role="img" aria-label="Brick family home with dark roof, trees and landscaped front garden"></div>
  <div class="brand"><b>Kelto</b> Construction</div>
  <nav class="nav">
    <a class="active">Home</a><a>About Us</a><a>Projects</a><a>Blog</a><a>Contact Us</a>
    <span class="search"><svg width="12" height="12" viewBox="0 0 12 12"><circle cx="5" cy="5" r="3.5" fill="none" stroke="#fff" stroke-width="1.6"/><line x1="7.6" y1="7.6" x2="11" y2="11" stroke="#fff" stroke-width="1.6"/></svg></span>
  </nav>
  <h1>Residential &amp; Commercial<br>Construction</h1>
  <a class="btn">Read More</a>
  <div class="dots"><span></span><span></span><span class="on"></span></div>
</header>

<section class="section services">
  <h2 class="title" style="top:54px">Our Services</h2>
  <div class="svc-grid">
    <div class="svc">
      <svg viewBox="0 0 80 72"><path d="M8 36 L40 8 L72 36" fill="none" stroke="#1b8fe2" stroke-width="5"/><rect x="16" y="34" width="48" height="34" fill="none" stroke="#1b8fe2" stroke-width="4"/><rect x="24" y="44" width="12" height="10" fill="#1b8fe2"/><rect x="44" y="44" width="12" height="24" fill="#1b8fe2"/><rect x="54" y="12" width="7" height="14" fill="#1b8fe2"/></svg>
      <h4>Residential Construction</h4><p>Lorem ipsum dolor sit amet, consectetur adipiscing elit, sed do eiusmod tem por incididunt ut labore et.</p>
    </div>
    <div class="svc">
      <svg viewBox="0 0 80 72"><rect x="10" y="10" width="28" height="60" fill="#1b8fe2"/><rect x="42" y="24" width="28" height="46" fill="#1b8fe2"/><g fill="#fff"><rect x="15" y="16" width="6" height="6"/><rect x="27" y="16" width="6" height="6"/><rect x="15" y="28" width="6" height="6"/><rect x="27" y="28" width="6" height="6"/><rect x="15" y="40" width="6" height="6"/><rect x="27" y="40" width="6" height="6"/><rect x="47" y="30" width="6" height="6"/><rect x="59" y="30" width="6" height="6"/><rect x="47" y="42" width="6" height="6"/><rect x="59" y="42" width="6" height="6"/><rect x="20" y="56" width="8" height="14"/><rect x="52" y="56" width="8" height="14"/></g></svg>
      <h4>Commercial Construction</h4><p>Lorem ipsum dolor sit amet, consectetur adipiscing elit, sed do eiusmod tem por incididunt ut labore et.</p>
    </div>
    <div class="svc">
      <svg viewBox="0 0 80 72"><path d="M18 36 A22 22 0 0 1 62 36 Z" fill="#1b8fe2"/><rect x="12" y="36" width="56" height="6" fill="#1b8fe2"/><rect x="36" y="10" width="8" height="26" fill="#fff" opacity=".5"/><path d="M14 70 Q40 48 66 70 Z" fill="#1b8fe2"/></svg>
      <h4>Construction Management</h4><p>Lorem ipsum dolor sit amet, consectetur adipiscing elit, sed do eiusmod tem por incididunt ut labore et.</p>
    </div>
    <div class="svc">
      <svg viewBox="0 0 80 72"><g transform="rotate(-45 40 36)"><rect x="10" y="28" width="60" height="16" fill="#1b8fe2"/><g stroke="#fff" stroke-width="2"><line x1="18" y1="28" x2="18" y2="36"/><line x1="26" y1="28" x2="26" y2="34"/><line x1="34" y1="28" x2="34" y2="36"/><line x1="42" y1="28" x2="42" y2="34"/><line x1="50" y1="28" x2="50" y2="36"/><line x1="58" y1="28" x2="58" y2="34"/></g></g><g transform="rotate(45 40 36)"><rect x="14" y="32" width="46" height="9" fill="#1477c4"/><path d="M60 32 L70 36.5 L60 41 Z" fill="#1477c4"/></g></svg>
      <h4>Design/Build</h4><p>Lorem ipsum dolor sit amet, consectetur adipiscing elit, sed do eiusmod tem por incididunt ut labore et.</p>
    </div>
    <div class="svc">
      <svg viewBox="0 0 80 72"><g transform="rotate(45 40 36)"><rect x="36" y="14" width="8" height="50" fill="#1b8fe2"/><path d="M28 6 H52 V20 H28 Z" fill="#1b8fe2"/></g><g transform="rotate(-45 40 36)"><rect x="36" y="18" width="8" height="48" fill="#1477c4"/><circle cx="40" cy="14" r="10" fill="#1477c4"/><rect x="37" y="2" width="6" height="12" fill="#fff"/></g></svg>
      <h4>Renovation</h4><p>Lorem ipsum dolor sit amet, consectetur adipiscing elit, sed do eiusmod tem por incididunt ut labore et.</p>
    </div>
    <div class="svc">
      <svg viewBox="0 0 80 72"><path d="M24 34 L40 20 L56 34 V56 H24 Z" fill="none" stroke="#1b8fe2" stroke-width="4"/><rect x="35" y="40" width="10" height="16" fill="#1b8fe2"/><g stroke="#1b8fe2" stroke-width="3" fill="none"><line x1="14" y1="10" x2="14" y2="62"/><path d="M9 16 L14 10 L19 16 M9 56 L14 62 L19 56"/><line x1="22" y1="66" x2="58" y2="66"/><path d="M28 61 L22 66 L28 71 M52 61 L58 66 L52 71"/></g></svg>
      <h4>Construction Consulting</h4><p>Lorem ipsum dolor sit amet, consectetur adipiscing elit, sed do eiusmod tem por incididunt ut labore et.</p>
    </div>
  </div>
</section>

<section class="section welcome">
  <div class="welcome-photo" role="img" aria-label="Lit stone villa at dusk against a violet sky and hills"></div>
  <div class="welcome-split"></div>
  <h3>Welcome to Our Site</h3>
  <p class="intro">Lorem ipsum dolor sit amet, consectetur adipiscing elit, sed do eiusmod tempor incididunt ut labore et dolore magna aliqua. Ut enim ad minim veniam, quis nostrud exercitation</p>
  <a class="btn-outline">Read More</a>
  <div class="feature" style="top:57px">
    <div class="ico"><svg width="34" height="28" viewBox="0 0 34 28"><circle cx="17" cy="8" r="6" fill="#fff"/><circle cx="6" cy="11" r="4" fill="#fff"/><circle cx="28" cy="11" r="4" fill="#fff"/><path d="M7 27 Q17 12 27 27 Z M0 26 Q6 15 12 22 Z M22 22 Q28 15 34 26 Z" fill="#fff"/></svg></div>
    <div><h4>Meet Team</h4><p>Lorem ipsum dolor sit amet, consectetur adipiscing elit, sed do eiusmod tem</p></div>
  </div>
  <div class="feature" style="top:177px">
    <div class="ico"><svg width="30" height="30" viewBox="0 0 30 30"><path d="M28 2 Q18 2 10 12 L18 20 Q28 12 28 2 Z" fill="#fff"/><path d="M10 12 L3 13 L7 8 Z M18 20 L17 27 L22 23 Z" fill="#fff"/><path d="M8 18 L3 27 L12 22 Z" fill="#fff"/></svg></div>
    <div><h4>Mission</h4><p>Lorem ipsum dolor sit amet, consectetur adipiscing elit, sed do eiusmod tem</p></div>
  </div>
  <div class="feature" style="top:295px">
    <div class="ico"><svg width="30" height="22" viewBox="0 0 30 22"><rect x="1" y="1" width="28" height="20" fill="#fff"/><path d="M1 1 L15 12 L29 1" fill="none" stroke="#8a84d8" stroke-width="2"/></svg></div>
    <div><h4>Contact Us</h4><p>Lorem ipsum dolor sit amet, consectetur adipiscing elit, sed do eiusmod tem</p></div>
  </div>
</section>

<section class="section projects">
  <h2 class="title" style="top:54px">Our Recent Projects</h2>
  <div class="proj-grid">
    <div class="proj p1" role="img" aria-label="Two-storey home with lit porch"></div>
    <div class="proj p2" role="img" aria-label="Suburban house with gabled roof and lawn"></div>
    <div class="proj p3" role="img" aria-label="Green-roofed home with white picket fence"></div>
    <div class="proj p4" role="img" aria-label="Glass office building under blue sky"></div>
    <div class="proj p5" role="img" aria-label="Curved glass commercial building at sunset"></div>
    <div class="proj p6" role="img" aria-label="Red brick multi-storey commercial building"></div>
  </div>
  <div class="ghost">PROJECTS</div>
  <a class="btn">View All</a>
</section>

<section class="section blog">
  <div class="blog-photo" role="img" aria-label="White house on a green lawn under a bright blue sky"></div>
  <h2 class="title light" style="top:63px">Latest Blog</h2>
  <div class="cards">
    <article class="card"><span class="num">1</span><h4>Lorem ipsum dolor sit amet consectetur</h4><p>Lorem ipsum dolor sit amet, consectetur adipiscing elit, sed do eiusmod tempor incididunt ut labore et. Nor again is there anyone who loves or pursues, or desires to obtain.</p><a class="btn">Read More</a></article>
    <article class="card"><span class="num">2</span><h4>Lorem ipsum dolor sit amet consectetur</h4><p>Lorem ipsum dolor sit amet, consectetur adipiscing elit, sed do eiusmod tempor incididunt ut labore et. Nor again is there anyone who loves or pursues, or desires to obtain.</p><a class="btn">Read More</a></article>
    <article class="card"><span class="num">3</span><h4>Lorem ipsum dolor sit amet consectetur</h4><p>Lorem ipsum dolor sit amet, consectetur adipiscing elit, sed do eiusmod tempor incididunt ut labore et. Nor again is there anyone who loves or pursues, or desires to obtain.</p><a class="btn">Read More</a></article>
  </div>
</section>

<footer class="section footer">
  <div class="brand"><b>Kelto</b> Construction</div>
  <div class="follow">FOLLOW US <span class="dot"></span><span class="dot"></span><span class="dot dark"></span></div>
  <div class="fcol contact-col">
    <h5>Contact Us</h5>
    <div class="row"><svg width="10" height="14" viewBox="0 0 10 14"><path d="M5 0 A5 5 0 0 1 10 5 C10 9 5 14 5 14 C5 14 0 9 0 5 A5 5 0 0 1 5 0 Z" fill="#fff"/><circle cx="5" cy="5" r="2" fill="#1b8fe2"/></svg><span>18 Harbour Works Road<br>Auckland 1010</span></div>
    <div class="row"><svg width="12" height="12" viewBox="0 0 12 12"><path d="M2 0 L5 3 L3.5 5 Q5 7.5 7 8.5 L9 7 L12 10 L10 12 Q3 11 0 2 Z" fill="#fff"/></svg><span>09 555 0142</span></div>
    <div class="row"><svg width="13" height="10" viewBox="0 0 13 10"><rect width="13" height="10" fill="#fff"/><path d="M0 0 L6.5 5 L13 0" fill="none" stroke="#1b8fe2" stroke-width="1.2"/></svg><span>info@kelto.example.nz</span></div>
  </div>
  <div class="fcol menu-col">
    <h5>Menu</h5>
    <a>Home</a><a>About us</a><a>Projects</a><a>Blog</a><a>Contact us</a>
  </div>
  <div class="map" role="img" aria-label="Street map showing the office location"></div>
  <div class="rule"></div>
  <p class="copy">Copyrights @ 2018 All Rights Reserved</p>
</footer>

</body>
</html>
```